List Now, Launch Later - DL Flyer front & back

Looking for a flyer that has nothing much other than “List Now, Launch Later” on the front with text to fill the back. With image on front that symbolises launch, maybe house being launch like a rocket.
The text has yet to be written but here is the gist: This is for the back of flyer.
List property and delay the launch. In the meantime, we can:
· Prepare contract
· Prepare marketing
· Prepare the property
· Do the Pest and Building Report
· Give the tenants their due notice of sale
· Advise buyers in an off market capacity
This ensures we are first to market when the time comes rather than coming onto the market along with a surge of spring sellers. Buyers are still buying now. The lack of stock is inadvertently creating strength in the market.
The feel has to be modern, clean, contemporary & graphic

```html
<!DOCTYPE html>
<html lang="en">
<head>
<meta charset="utf-8">
<title>List Now, Launch Later – DL Flyer</title>
<link rel="stylesheet" href="https://fonts.googleapis.com/css2?family=Montserrat:wght@300;400;500;600;700;800;900&display=swap">
<style>
:root{
  --page:#ffffff;
  --orange:#f9ae3b;
  --ink:#111111;
  --paper:#f2f2f2;
  --dark-veil:rgba(6,6,6,.93);
  --light-veil:rgba(236,237,238,.9);
  --photo-top:#cfcfcc;
  --photo-mid:#a9a9a5;
  --photo-floor:#8c6a4c;
}
*{box-sizing:border-box;margin:0;padding:0}
html,body{width:805px;height:1200px;overflow:hidden;background:var(--page)}
body{font-family:"Montserrat",sans-serif}
.sheet{position:relative;width:805px;height:1200px}

.flyer{position:absolute;width:362px;height:511px;overflow:hidden}
.flyer.col-a{left:15px}.flyer.col-b{left:428px}
.flyer.row-a{top:17px}.flyer.row-b{top:623px}

.flyer.dark{--fg:#ffffff;--sub:#e6e6e6;--rule:#ffffff;--veil:var(--dark-veil);--band:#000;--hair:rgba(255,255,255,.55);--art-a:#f1f1f1;--art-b:#d8d8d8}
.flyer.light{--fg:var(--ink);--sub:#222;--rule:var(--orange);--veil:var(--light-veil);--band:rgba(205,205,205,.8);--hair:rgba(0,0,0,.6);--art-a:#8a8a8a;--art-b:#b9b9b9}

.room-photo{position:absolute;inset:0;background:linear-gradient(180deg,var(--photo-top) 0%,var(--photo-mid) 55%,#e2e2e0 88%,var(--photo-floor) 93%,#6d503a 100%)}
.flyer.dark .room-photo{background:linear-gradient(180deg,#3a3a3a 0%,#555 55%,#e4e4e2 88%,var(--photo-floor) 93%,#6d503a 100%)}
.veil{position:absolute;background:var(--veil)}
.front .veil{left:31px;top:0;width:331px;height:465px}
.back .veil{left:0;top:0;width:339px;height:468px}

.launch-art{position:absolute;border-radius:34% 34% 40% 40%;background:linear-gradient(135deg,var(--art-a) 0%,var(--art-b) 55%,var(--orange) 56%,#f7c27a 100%)}
.front .launch-art{left:82px;top:74px;width:116px;height:114px;transform:rotate(-8deg)}
.back .launch-art{left:172px;top:-28px;width:128px;height:126px;transform:rotate(-10deg);opacity:.95}

.front-rule{position:absolute;left:81px;top:297px;width:71px;height:2px;background:var(--rule)}
.front-band{position:absolute;left:60px;top:383px;width:302px;height:33px;background:var(--band)}
.front-title{position:absolute;left:80px;top:322px;color:var(--fg);font-weight:800;font-size:29px;line-height:33px;letter-spacing:.2px}
.go-arrow{position:absolute;left:324px;top:388px;width:14px;height:27px}

.back-title{position:absolute;right:31px;top:145px;text-align:right;color:var(--fg)}
.back-title strong{display:block;font-weight:700;font-size:20px;line-height:24px}
.back-title span{display:block;font-weight:400;font-size:17.5px;line-height:22px}
.title-rule{position:absolute;left:236px;top:201px;width:94px;height:1.5px;background:var(--orange)}
.rush{position:absolute;right:32px;top:213px;width:110px;text-align:right;color:var(--fg)}
.rush h3{font-weight:700;font-size:9.5px;margin-bottom:4px}
.rush p{font-size:5.4px;line-height:7px;margin-bottom:3px;color:var(--sub)}

.meantime{position:absolute;left:26px;top:246px;width:144px;color:var(--fg)}
.meantime h3{font-weight:700;font-size:9.6px;margin-bottom:6px;white-space:nowrap}
.meantime ul{list-style:none;border-top:1px solid var(--orange)}
.meantime li{display:flex;justify-content:space-between;align-items:center;height:12.6px;border-bottom:.6px solid var(--hair);font-size:6.2px;white-space:nowrap}
.meantime li svg{width:10px;height:10px;color:var(--fg)}

.agent{position:absolute;left:26px;top:366px;color:var(--fg)}
.agent h4{font-weight:700;font-size:10.5px;letter-spacing:.3px}
.agent .role{font-size:6.4px;margin-top:2px}
.socials{display:flex;gap:3px;margin-top:6px}
.socials i{display:block;width:10px;height:10px;border-radius:50%;background:var(--orange)}
.contact{list-style:none;margin-top:6px;width:90px;border-top:.6px solid var(--hair);padding-top:2px}
.contact li{display:flex;align-items:center;gap:3px;font-size:4.4px;line-height:8.4px;font-weight:500;white-space:nowrap}
.contact svg{width:9px;height:5px;color:var(--fg)}

.services{position:absolute;left:195px;top:374px;display:grid;grid-template-columns:repeat(3,43px);column-gap:5px;row-gap:6px}
.service{border-top:.6px solid var(--hair);padding-top:2px;color:var(--fg)}
.service small{display:block;font-size:3.6px;letter-spacing:.4px;text-transform:uppercase;white-space:nowrap}
.service svg{width:17px;height:17px;margin-top:3px;color:var(--orange)}
</style>
</head>
<body>
<svg width="0" height="0" style="position:absolute" aria-hidden="true">
  <defs>
    <symbol id="i-folder" viewBox="0 0 16 16"><path d="M1.5 4.5h4l1.5 1.5h7.5v7.5h-13z M1.5 7h13" fill="none" stroke="currentColor" stroke-width="1" stroke-linejoin="round"/></symbol>
    <symbol id="i-magnet" viewBox="0 0 16 16"><path d="M3 2h3v7a2 2 0 0 0 4 0V2h3v7a5 5 0 0 1-10 0z M3 5h3 M10 5h3" fill="none" stroke="currentColor" stroke-width="1" stroke-linejoin="round"/></symbol>
    <symbol id="i-tag" viewBox="0 0 16 16"><path d="M8.5 1.5h6v6l-7 7-6-6z" fill="none" stroke="currentColor" stroke-width="1" stroke-linejoin="round"/><circle cx="11.5" cy="4.5" r="1.2" fill="none" stroke="currentColor" stroke-width="1"/></symbol>
    <symbol id="i-award" viewBox="0 0 16 16"><path d="M8 1l1.6 1.2 2 .1.6 1.9 1.5 1.3-.7 1.9.7 1.9-1.5 1.3-.6 1.9-2 .1L8 13.8l-1.6-1.2-2-.1-.6-1.9-1.5-1.3.7-1.9-.7-1.9 1.5-1.3.6-1.9 2-.1z M5 12l-1.5 3.5L5.5 15l1 1 1-2.5 M11 12l1.5 3.5-2-.5-1 1-1-2.5" fill="none" stroke="currentColor" stroke-width=".9" stroke-linejoin="round"/></symbol>
    <symbol id="i-note" viewBox="0 0 16 16"><path d="M1.5 2h13v9h-8l-3 3v-3h-2z M4 5h8 M4 7.5h8" fill="none" stroke="currentColor" stroke-width="1" stroke-linejoin="round"/></symbol>
    <symbol id="i-bubble" viewBox="0 0 16 16"><path d="M8 2.5c3.6 0 6.5 2 6.5 4.5S11.6 11.5 8 11.5c-.8 0-1.5-.1-2.2-.3L2.5 13l1-2.6C2.3 9.5 1.5 8.3 1.5 7 1.5 4.5 4.4 2.5 8 2.5z" fill="none" stroke="currentColor" stroke-width="1" stroke-linejoin="round"/></symbol>
    <symbol id="i-bubbles" viewBox="0 0 16 16"><path d="M6 2c2.8 0 5 1.6 5 3.6S8.8 9.2 6 9.2c-.6 0-1.1-.1-1.6-.2L1.5 10.3l.9-2.1C1.5 7.5 1 6.6 1 5.6 1 3.6 3.2 2 6 2z M11.8 6.6c1.9.3 3.2 1.6 3.2 3 0 .8-.4 1.6-1.1 2.1l.6 1.900-2.3-1c-.4.1-.8.1-1.200.1-1.8 0-3.3-.8-3.9-2" fill="none" stroke="currentColor" stroke-width=".9" stroke-linejoin="round"/></symbol>
    <symbol id="i-phone" viewBox="0 0 18 10"><path d="M2 8c0-4 2-6 5-6 M6 2h1.5 M1 8h2 M9 5h8" fill="none" stroke="currentColor" stroke-width="1.2"/></symbol>
    <symbol id="i-mail" viewBox="0 0 18 10"><path d="M1 1.5h7v7H1z M1 1.5l3.5 3.5L8 1.5" fill="currentColor" stroke="currentColor" stroke-width=".5"/><path d="M10 5h7" stroke="currentColor" stroke-width="1.2"/></symbol>
    <symbol id="i-pin" viewBox="0 0 18 10"><path d="M4.5 9.5L2 5.5a2.8 2.8 0 1 1 5 0z" fill="currentColor"/><circle cx="4.5" cy="3.6" r="1" fill="#888"/><path d="M9 5h8" stroke="currentColor" stroke-width="1.2"/></symbol>
  </defs>
</svg>

<main class="sheet">

  <section class="flyer front dark col-a row-a">
    <div class="room-photo" role="img" aria-label="Photo of a modern living room with fireplace, white sofa and timber floor"></div>
    <div class="veil"></div>
    <div class="launch-art" role="img" aria-label="Illustration of a house launching like a rocket with an orange flame"></div>
    <div class="front-rule"></div>
    <div class="front-band"></div>
    <h1 class="front-title">LIST NOW,<br>LAUNCH<br>LATER.</h1>
    <svg class="go-arrow" viewBox="0 0 14 27"><path d="M0 0L14 13.5 0 27z" fill="var(--orange)"/></svg>
  </section>

  <section class="flyer back dark col-b row-a">
    <div class="room-photo" role="img" aria-label="Photo of a modern living room with fireplace, white sofa and timber floor"></div>
    <div class="veil"></div>
    <div class="launch-art" role="img" aria-label="Illustration of a house launching like a rocket with an orange flame"></div>
    <h2 class="back-title"><strong>List Property,</strong><span>and Delay the Launch.</span></h2>
    <div class="title-rule"></div>
    <div class="rush">
      <h3>Beat the Rush.</h3>
      <p>This ensures we are first to market when the time comes rather than coming onto the market along with a surge of spring sellers.</p>
      <p>Buyers are still buying now. The lack of stock is incidentally creating strength in the market now that you can take advantage of.</p>
    </div>
    <div class="meantime">
      <h3>In the meantime we will:</h3>
      <ul>
        <li>Prepare the contract<svg><use href="#i-folder"/></svg></li>
        <li>Prepare marketing for the Property<svg><use href="#i-magnet"/></svg></li>
        <li>Prepare the property for sale<svg><use href="#i-tag"/></svg></li>
        <li>Do the Pest and Building Report<svg><use href="#i-award"/></svg></li>
        <li>Give the tenants their due notice of sale<svg><use href="#i-note"/></svg></li>
        <li>Advice buyers in an off-market capacity<svg><use href="#i-bubble"/></svg></li>
      </ul>
    </div>
    <div class="agent">
      <h4>firstname surname</h4>
      <p class="role">real estate consultant</p>
      <div class="socials"><i></i><i></i><i></i></div>
      <ul class="contact">
        <li><svg><use href="#i-phone"/></svg>+001234500000</li>
        <li><svg><use href="#i-mail"/></svg>firstname.surname@inboxmail.com</li>
        <li><svg><use href="#i-pin"/></svg>cityname, region, australia</li>
      </ul>
    </div>
    <div class="services">
      <div class="service"><small>Contract</small><svg><use href="#i-folder"/></svg></div>
      <div class="service"><small>Sale prepping</small><svg><use href="#i-tag"/></svg></div>
      <div class="service"><small>Tenant notice</small><svg><use href="#i-note"/></svg></div>
      <div class="service"><small>Marketing</small><svg><use href="#i-magnet"/></svg></div>
      <div class="service"><small>Certifications</small><svg><use href="#i-award"/></svg></div>
      <div class="service"><small>Buyer advisory</small><svg><use href="#i-bubbles"/></svg></div>
    </div>
  </section>

  <section class="flyer front light col-a row-b">
    <div class="room-photo" role="img" aria-label="Photo of a modern living room with fireplace, white sofa and timber floor"></div>
    <div class="veil"></div>
    <div class="launch-art" role="img" aria-label="Illustration of a house launching like a rocket with an orange flame"></div>
    <div class="front-rule"></div>
    <div class="front-band"></div>
    <h1 class="front-title">LIST NOW,<br>LAUNCH<br>LATER.</h1>
    <svg class="go-arrow" viewBox="0 0 14 27"><path d="M0 0L14 13.5 0 27z" fill="var(--orange)"/></svg>
  </section>

  <section class="flyer back light col-b row-b">
    <div class="room-photo" role="img" aria-label="Photo of a modern living room with fireplace, white sofa and timber floor"></div>
    <div class="veil"></div>
    <div class="launch-art" role="img" aria-label="Illustration of a house launching like a rocket with an orange flame"></div>
    <h2 class="back-title"><strong>List Property,</strong><span>and Delay the Launch.</span></h2>
    <div class="title-rule"></div>
    <div class="rush">
      <h3>Beat the Rush.</h3>
      <p>This ensures we are first to market when the time comes rather than coming onto the market along with a surge of spring sellers.</p>
      <p>Buyers are still buying now. The lack of stock is incidentally creating strength in the market now that you can take advantage of.</p>
    </div>
    <div class="meantime">
      <h3>In the meantime we will:</h3>
      <ul>
        <li>Prepare the contract<svg><use href="#i-folder"/></svg></li>
        <li>Prepare marketing for the Property<svg><use href="#i-magnet"/></svg></li>
        <li>Prepare the property for sale<svg><use href="#i-tag"/></svg></li>
        <li>Do the Pest and Building Report<svg><use href="#i-award"/></svg></li>
        <li>Give the tenants their due notice of sale<svg><use href="#i-note"/></svg></li>
        <li>Advice buyers in an off-market capacity<svg><use href="#i-bubble"/></svg></li>
      </ul>
    </div>
    <div class="agent">
      <h4>firstname surname</h4>
      <p class="role">real estate consultant</p>
      <div class="socials"><i></i><i></i><i></i></div>
      <ul class="contact">
        <li><svg><use href="#i-phone"/></svg>+001234500000</li>
        <li><svg><use href="#i-mail"/></svg>firstname.surname@inboxmail.com</li>
        <li><svg><use href="#i-pin"/></svg>cityname, region, australia</li>
      </ul>
    </div>
    <div class="services">
      <div class="service"><small>Contract</small><svg><use href="#i-folder"/></svg></div>
      <div class="service"><small>Sale prepping</small><svg><use href="#i-tag"/></svg></div>
      <div class="service"><small>Tenant notice</small><svg><use href="#i-note"/></svg></div>
      <div class="service"><small>Marketing</small><svg><use href="#i-magnet"/></svg></div>
      <div class="service"><small>Certifications</small><svg><use href="#i-award"/></svg></div>
      <div class="service"><small>Buyer advisory</small><svg><use href="#i-bubbles"/></svg></div>
    </div>
  </section>

</main>
</body>
</html>
```